Bed Company needs business card

Hello, we are a bed company that makes specialized magnets for beds. We are an alternative healing company. I need a modern and upscale business card. Please incorporate my logo for the card.

Accepted file formats are AI, EPS, and Press-Ready PDFS.

Please include all fonts or convert them to outlines regardless of file type.

If you are designing the card in Photoshop the file Must be 1200dpi.

I am open to anything for the business card.  I really like all of your designs and if you want to change the color of the logo, you can.  I will be making the final selection by Friday.  Thank You for all of your designs.  Feel Free to submit different color logos if you want.  

Reason: I will make a decision Final on Friday April 20th. 2012. Good Luck and Thank you all for the designs.

Target Market(s)

My target Market is people, who are looking for alternative healing.

Industry/Entity Type

Business

Requirements
Must have
• My logo must be incorporated. The front card must have

Name
Job Title

Address
Work
Cell
Fax
email
web

Just put in fake info for the card.

The back of the card. I want the logo on the back with color. I just want it to look modern and cool.

```html
<!DOCTYPE html>
<html lang="en">
<head>
<meta charset="utf-8">
<title>Restora Bed – Business Card</title>
<link rel="stylesheet" href="https://fonts.googleapis.com/css2?family=Source+Sans+3:wght@400;600&display=swap">
<style>
  :root {
    --backdrop: #e6e6e6;
    --card: #ffffff;
    --green-deep: #0e5a1e;
    --green-mid: #1f8a2e;
    --green-bright: #2f9e3c;
    --green-logo: #3aaa4a;
    --band: #107a28;
    --photo-light: #e9e3d6;
    --photo-dark: #a98a62;
  }
  * { box-sizing: border-box; margin: 0; padding: 0; }
  html, body {
    width: 1200px; height: 911px; overflow: hidden;
    background: var(--backdrop);
    font-family: "Source Sans 3", sans-serif;
  }
  .canvas { position: relative; width: 1200px; height: 911px; }
  .card {
    position: absolute;
    background: var(--card);
    box-shadow: 7px 7px 5px rgba(0,0,0,0.6);
    overflow: hidden;
  }
  .card--front { left: 71px; top: 38px; width: 666px; height: 381px; }
  .card--back  { left: 483px; top: 471px; width: 665px; height: 378px; }

  .holder-name {
    position: absolute; left: 55px; top: 39px;
    font-size: 23px; font-weight: 600; color: var(--green-deep);
  }
  .holder-title {
    position: absolute; left: 59px; top: 67px;
    font-size: 14px; color: var(--green-bright);
  }
  .bedroom-photo {
    position: absolute; left: 353px; top: 22px; width: 303px; height: 108px;
  }
  .details {
    position: absolute; left: 41px; top: 211px;
    font-size: 16px; line-height: 25px; color: var(--green-mid);
  }
  .details .label { display: inline-block; width: 96px; }
  .details .label--short { width: auto; margin-right: 6px; }
  .phones {
    position: absolute; left: 447px; top: 208px;
    font-size: 18px; line-height: 25px; color: var(--green-deep);
  }
  .web {
    position: absolute; left: 0; width: 604px; top: 310px;
    text-align: center; font-size: 18px; line-height: 25px; color: var(--green-deep);
  }
  .band {
    position: absolute; left: 0; bottom: 0; width: 100%; height: 13px;
    background: var(--band);
  }

  .brand-mark {
    position: absolute; left: 13px; top: 142px; width: 44px; height: 44px;
    background: var(--band);
  }
  .brand-name {
    position: absolute; left: 68px; top: 124px;
    font-size: 60px; font-weight: 600; line-height: 1; color: var(--green-logo);
  }
  .brand-tagline {
    position: absolute; left: 157px; top: 206px;
    font-size: 19px; color: var(--green-mid);
  }
  .edge-pattern {
    position: absolute; left: 567px; top: 0; width: 98px; height: 100%;
  }
</style>
</head>
<body>
<main class="canvas">
  <section class="card card--front" aria-label="Card front">
    <h1 class="holder-name">DANIEL REYES</h1>
    <p class="holder-title">MANAGING DIRECTOR</p>
    <svg class="bedroom-photo" role="img" aria-label="Photo of a bright bedroom with a made bed" viewBox="0 0 303 108" preserveAspectRatio="none">
      <defs>
        <linearGradient id="room" x1="0" y1="0" x2="0" y2="1">
          <stop offset="0" stop-color="var(--photo-light)"/>
          <stop offset="0.6" stop-color="#d9cfbf"/>
          <stop offset="1" stop-color="var(--photo-dark)"/>
        </linearGradient>
      </defs>
      <rect width="303" height="108" fill="url(#room)"/>
    </svg>
    <div class="details">
      <p><span class="label">ADDRESS:</span>LINDEN SQUARE</p>
      <p><span class="label label--short">WORK:</span>ALTERNATIVE HEALING COMPANY</p>
    </div>
    <div class="phones">
      <p>CELL: 047218390</p>
      <p>FAX: 08451327094</p>
    </div>
    <div class="web">
      <p>DANIEL@RESTORABED.COM</p>
      <p>WWW.RESTORABED.COM</p>
    </div>
    <div class="band"></div>
  </section>

  <section class="card card--back" aria-label="Card back">
    <span class="brand-mark"></span>
    <p class="brand-name">Restora Bed</p>
    <p class="brand-tagline">Alternative Healing</p>
    <svg class="edge-pattern" role="img" aria-label="Green decorative zigzag pattern along the right edge" viewBox="0 0 98 378" preserveAspectRatio="none">
      <defs>
        <linearGradient id="edge" x1="0" y1="0" x2="1" y2="0">
          <stop offset="0" stop-color="#ffffff"/>
          <stop offset="0.5" stop-color="#5aa768"/>
          <stop offset="1" stop-color="var(--band)"/>
        </linearGradient>
      </defs>
      <rect width="98" height="378" fill="url(#edge)"/>
    </svg>
  </section>
</main>
</body>
</html>
```